Quillbrookes websites redesign

Www.quill-brookes.com needs to be redesigned along with updations. The incremental material will be provided for the updations. We are looking for complete redesign of the pages with the new content. The complete write up will be provided soon

Target Market(s)

Global

Coding

Coded - Design and coding required

Number of Pages Required

5+ page

Requirements
Must have
• A clean and slick design for the Consulting.
Should not have
• Too many pictures which reduces the speed of the site

```html
<!DOCTYPE html>
<html lang="en">
<head>
<meta charset="utf-8">
<title>Quillbrookes Consultancy</title>
<link rel="stylesheet" href="https://fonts.googleapis.com/css2?family=Raleway:wght@500;600;700&family=Open+Sans:ital,wght@0,400;0,600;0,700;1,600&display=swap">
<style>
:root{
  --teal:#3aa3c8;
  --ink:#1f2a44;
  --maroon:#6b1e24;
  --text:#6d6d6d;
  --panel:#f2f2f2;
  --footer:#242424;
  --footer-text:#d4d4d4;
  --line:#d8d8d8;
}
*{box-sizing:border-box;margin:0;padding:0}
html,body{width:1200px;height:2550px;overflow:hidden;background:#fff}
body{position:relative;font-family:"Open Sans",sans-serif;color:var(--text)}
.abs{position:absolute}
.topbar{left:0;top:0;width:1200px;height:5px;background:var(--teal)}
.header{left:0;top:5px;width:1200px;height:83px;background:#fff}
.brand{display:flex;align-items:center;gap:12px;font-family:"Raleway",sans-serif;font-weight:600;color:var(--ink)}
.brand-dot{border-radius:50%;background:var(--maroon)}
.header .brand{position:absolute;left:97px;top:22px;font-size:33px}
.header .brand-dot{width:42px;height:42px}
.nav{position:absolute;top:33px;left:487px;display:flex;gap:0;font-family:"Raleway",sans-serif;font-weight:600;font-size:15px;color:var(--ink)}
.nav span{margin-right:25px}
.nav .active{color:var(--teal)}
.search{position:absolute;left:1062px;top:20px;width:38px;height:38px;border-radius:50%;background:var(--maroon)}
.hero{left:0;top:88px;width:1200px;height:434px;background:radial-gradient(ellipse at 55% 95%,#3d6f94 0%,#173049 35%,#0a1522 70%,#060c14 100%)}
.hero-title{left:0;top:160px;width:1200px;text-align:center;font-family:"Raleway",sans-serif;font-weight:500;font-size:58px;color:#fff;text-shadow:0 2px 6px rgba(0,0,0,.6)}
.dots{left:566px;top:474px;display:flex;gap:4px}
.dots i{width:13px;height:13px;border-radius:50%;border:2px solid #fff}
.dots i.on{background:var(--teal)}
.section-title{width:1200px;left:0;text-align:center;font-family:"Raleway",sans-serif;font-weight:700;color:#222}
.stats-title{top:564px;font-size:21px}
.stat{width:170px;height:170px;top:620px}
.stat svg{position:absolute;left:0;top:0}
.stat b{position:absolute;left:0;top:0;width:170px;line-height:170px;text-align:center;font-family:"Open Sans",sans-serif;font-weight:700;font-size:24px;color:var(--ink)}
.welcome-art{left:0;top:832px;width:600px;height:386px;background:linear-gradient(135deg,#49b4de,#2c96c4 60%,#3aa7d2)}
.welcome{left:600px;top:832px;width:600px;height:386px;background:var(--panel)}
.block-title{font-family:"Raleway",sans-serif;font-weight:700;font-size:21px;color:#222}
.copy{font-size:11.5px;line-height:25.5px;color:var(--text)}
.more{font-family:"Raleway",sans-serif;font-weight:700;font-size:12px;color:var(--maroon);letter-spacing:.3px}
.welcome .block-title{position:absolute;left:48px;top:40px}
.welcome .copy{position:absolute;left:52px;width:456px}
.welcome .more{position:absolute;left:50px;top:368px}
.cases-title{top:1308px;font-size:21px}
.cases-sub{left:0;top:1347px;width:1200px;text-align:center;font-style:italic;font-weight:600;font-size:13.5px;color:var(--teal)}
.case{top:1404px;width:241px;height:165px;border:1px solid var(--line);padding:4px;background:#fff}
.case div{width:100%;height:100%}
.case-cap{top:1586px;width:241px;text-align:center;font-family:"Raleway",sans-serif;font-weight:600;font-size:14px;line-height:23px;color:#222}
.founder-band{left:0;top:1680px;width:1200px;height:352px;background:var(--panel)}
.founder-photo{left:99px;top:1680px;width:301px;height:352px;background:linear-gradient(160deg,#6a4a2e,#2a1f1d 55%,#7a3a20)}
.founder{left:459px;top:1680px;width:650px;height:352px}
.founder .block-title{position:absolute;left:0;top:36px}
.founder .copy{position:absolute;left:3px;width:640px}
.founder .more{position:absolute;left:3px;top:290px}
.partner{top:2081px;width:185px;height:90px;border:1px solid var(--line);display:flex;align-items:center;justify-content:center}
.partner span{width:120px;height:30px;border-radius:4px;background:#d6dde4}
.footer{left:0;top:2216px;width:1200px;height:334px;background:var(--footer);color:var(--footer-text)}
.f-head{position:absolute;top:38px;font-family:"Raleway",sans-serif;font-weight:700;font-size:15px;color:#fff}
.f-list{position:absolute;top:72px;font-size:12px;line-height:24.7px}
.f-list li{list-style:none}
.f-note{position:absolute;left:287px;top:70px;width:300px;font-size:12px;line-height:21px}
.f-input{position:absolute;left:287px;top:123px;width:300px;height:33px;background:#fff;font-size:11px;color:#999;padding:9px 14px}
.f-btn{position:absolute;left:287px;top:180px;width:98px;height:34px;border:2px solid #fff;background:var(--teal);color:#fff;font-family:"Raleway",sans-serif;font-weight:700;font-size:11px;text-align:center;line-height:30px;letter-spacing:.5px}
.contact{position:absolute;left:879px;font-size:12px;line-height:16px}
.contact svg{position:absolute;left:0;top:1px}
.contact p{margin-left:35px;width:200px}
.f-rule{position:absolute;left:97px;top:248px;width:1006px;height:1px;background:#3a3a3a}
.footer .brand{position:absolute;left:95px;top:277px;font-size:24px;color:#fff;gap:10px}
.footer .brand-dot{width:30px;height:30px;background:#fff}
.copyright{position:absolute;left:0;top:285px;width:1200px;text-align:center;font-size:12px}
.social{position:absolute;left:936px;top:275px;display:flex;gap:12px}
.social i{width:37px;height:37px;border-radius:50%;border:2px solid #fff}
</style>
</head>
<body>
<div class="abs topbar"></div>
<header class="abs header">
  <div class="brand"><span class="brand-dot"></span>Quillbrookes</div>
  <nav class="nav"><span class="active">Home</span><span>Founder</span><span>Consultancy</span><span>System</span><span>Case Studies</span><span>Contact Us</span></nav>
  <div class="search" aria-label="Search"><svg width="38" height="38" viewBox="0 0 38 38"><circle cx="17" cy="17" r="6" fill="none" stroke="#fff" stroke-width="2.5"/><line x1="21.5" y1="21.5" x2="26" y2="26" stroke="#fff" stroke-width="2.5" stroke-linecap="round"/></svg></div>
</header>

<section class="abs hero" role="img" aria-label="Night view of the globe from space with glowing trade routes"></section>
<h1 class="abs hero-title">Global Trade Outlook</h1>
<div class="abs dots"><i class="on"></i><i></i><i></i><i></i></div>

<h2 class="abs section-title stats-title">World Merchandising Trade 2012 ( USD Billion)</h2>
<div class="abs stat" style="left:136px"><svg width="170" height="170"><circle cx="85" cy="85" r="80" fill="none" stroke="var(--ink)" stroke-width="2"/><circle cx="85" cy="85" r="80" fill="none" stroke="var(--teal)" stroke-width="7" stroke-dasharray="200 303" transform="rotate(-20 85 85)"/></svg><b>0 - 250</b></div>
<div class="abs stat" style="left:391px"><svg width="170" height="170"><circle cx="85" cy="85" r="80" fill="none" stroke="var(--ink)" stroke-width="2"/><circle cx="85" cy="85" r="80" fill="none" stroke="var(--teal)" stroke-width="7" stroke-dasharray="300 203" transform="rotate(-10 85 85)"/></svg><b>250 - 500</b></div>
<div class="abs stat" style="left:639px"><svg width="170" height="170"><circle cx="85" cy="85" r="80" fill="none" stroke="var(--ink)" stroke-width="2"/><circle cx="85" cy="85" r="80" fill="none" stroke="var(--teal)" stroke-width="7" stroke-dasharray="330 173" transform="rotate(-75 85 85)"/></svg><b>500 - 1000</b></div>
<div class="abs stat" style="left:891px"><svg width="170" height="170"><circle cx="85" cy="85" r="80" fill="none" stroke="var(--ink)" stroke-width="2"/><circle cx="85" cy="85" r="80" fill="none" stroke="var(--teal)" stroke-width="7" stroke-dasharray="160 343" transform="rotate(-220 85 85)"/></svg><b>&gt; 1000</b></div>

<div class="abs welcome-art" role="img" aria-label="Illustration of a world map with business people, charts and strategy sketches"></div>
<section class="abs welcome">
  <h2 class="block-title">Welcome to Quillbrookes</h2>
  <p class="copy" style="top:82px">Quillbrookes Consultancy Limited capitalizes on synergies arising from trade and investment linkages between countries and knowledge of traditional and non-traditional pools of liquidity to provide consultancy services to Emerging country banks, Corporates and SMEs.</p>
  <p class="copy" style="top:185px">The Consultancy provides bank neutral views to Corporates and SMEs in Asian emerging markets and helps in improving financial structure and efficient use of funds. Our endeavor is to provide a distinct bottom line advantage to our clients. The primary focus is in regionalisation of the banking relationship across the globe, providing structured finance solutions and off balance sheet solutions.</p>
  <a class="more">READ MORE &gt;&gt;</a>
</section>

<h2 class="abs section-title cases-title">Case Studies</h2>
<p class="abs cases-sub">Some of the deals completed by QCL are summarised below to describe the range of activities undertaken with Corporates</p>
<div class="abs case" style="left:97px"><div role="img" aria-label="Businessman facing a wall of rising bar charts" style="background:linear-gradient(160deg,#cfe3f3,#6f9fc9)"></div></div>
<div class="abs case" style="left:353px"><div role="img" aria-label="Businessman holding a tablet over a world map" style="background:linear-gradient(160deg,#e4e6e9,#9aa3ad)"></div></div>
<div class="abs case" style="left:608px"><div role="img" aria-label="Hands holding a glowing network of people" style="background:linear-gradient(160deg,#1d2f45,#4a7aa8)"></div></div>
<div class="abs case" style="left:861px"><div role="img" aria-label="Businessman working at a laptop with charts behind" style="background:linear-gradient(160deg,#eef0ee,#b7bcc2)"></div></div>
<p class="abs case-cap" style="left:97px">Export Credit Agency backed<br>long term Project financing</p>
<p class="abs case-cap" style="left:353px">Structured Financing</p>
<p class="abs case-cap" style="left:608px">Local banks for International<br>Subsidiary Banking</p>
<p class="abs case-cap" style="left:861px">Bank Lines Business</p>

<div class="abs founder-band"></div>
<div class="abs founder-photo" role="img" aria-label="Founder speaking at a podium during a conference"></div>
<section class="abs founder">
  <h2 class="block-title">Meera Talwar</h2>
  <p class="copy" style="top:82px">Ms. Meera Talwar is the founder director of Quillbrookes Consultancy Limited (QCL) based at Hong Kong. Meera worked as the Alternate Chief Executive of Northgate Bank, Hong Kong Branch until Jan 2013, heading Corporate Banking business in North Asia and Export Credit Agency business globally. During her tenure, both the businesses increased multifold.</p>
  <p class="copy" style="top:190px">Meera started her banking career with Northgate Bank Ltd, India's second largest bank in the year 2002 and in the next 10 years handled multiple leadership responsibilities in the Corporate.</p>
  <a class="more">READ MORE &gt;&gt;</a>
</section>

<div class="abs partner" style="left:97px"><span></span></div>
<div class="abs partner" style="left:303px"><span></span></div>
<div class="abs partner" style="left:507px"><span></span></div>
<div class="abs partner" style="left:713px"><span></span></div>
<div class="abs partner" style="left:918px"><span></span></div>

<footer class="abs footer">
  <h3 class="f-head" style="left:99px">INFORMATION</h3>
  <ul class="f-list" style="left:99px"><li>Home</li><li>Founder</li><li>Consultancy</li><li>System</li><li>Case Studies</li><li style="margin-top:6px">Contact Us</li></ul>
  <h3 class="f-head" style="left:287px">NEWSLETTER SUBSCRIPTION</h3>
  <p class="f-note">Register your email address to get information about us</p>
  <div class="f-input">Email Address</div>
  <div class="f-btn">SUBSCRIBE</div>
  <h3 class="f-head" style="left:682px">QUICK LINKS</h3>
  <ul class="f-list" style="left:682px"><li>Query</li><li>Help</li><li>FAQ</li><li>Privacy Policy</li><li>Terms &amp; Conditions</li><li>System</li></ul>
  <h3 class="f-head" style="left:879px">CONTACT US</h3>
  <div class="contact" style="top:74px"><svg width="12" height="14" viewBox="0 0 12 14"><path d="M6 0a5 5 0 0 0-5 5c0 4 5 9 5 9s5-5 5-9a5 5 0 0 0-5-5zm0 7a2 2 0 1 1 0-4 2 2 0 0 1 0 4z" fill="#fff"/></svg><p>Unit 04, 9th Floor, Harbour Exchange Tower, 18 Lantern Road, Kowloon, Hong Kong</p></div>
  <div class="contact" style="top:146px"><svg width="13" height="13" viewBox="0 0 13 13"><path d="M3 0l2 3-1.5 1.5a8 8 0 0 0 5 5L10 8l3 2-1.5 3C6 13 0 7 0 1.5z" fill="#fff"/></svg><p>+852-2100 4417</p></div>
  <div class="contact" style="top:177px"><svg width="14" height="13" viewBox="0 0 14 13"><rect x="0" y="3" width="14" height="10" rx="1" fill="#fff"/><rect x="3" y="0" width="8" height="4" fill="#fff"/><rect x="3" y="6" width="8" height="4" fill="#242424"/></svg><p>+852-2100 4418</p></div>
  <div class="contact" style="top:208px"><svg width="14" height="11" viewBox="0 0 14 11"><rect width="14" height="11" rx="1" fill="#fff"/><path d="M0 1l7 5 7-5" fill="none" stroke="#242424" stroke-width="1.4"/></svg><p>query@quill-brookes.com</p></div>
  <div class="f-rule"></div>
  <div class="brand"><span class="brand-dot"></span>Quillbrookes</div>
  <p class="copyright">Copyrights © 2016, Quill - Brookes. All rights reserved.</p>
  <div class="social" aria-label="Social links"><i></i><i></i><i></i><i></i></div>
</footer>
</body>
</html>
```